Brellwick Partners, LLC Stationary

Brellwick Partners, LLC is a new financial planning and consulting company. We are looking for designs on business cards, letterhead, envelopes, and anything else that would be useful. Our preference for business card design is two sided. We are looking for a professional and clean look with incorporating the logo and patriotic feel. Thank you to all who participate and good luck!

```html
<!DOCTYPE html>
<html lang="en">
<head>
<meta charset="utf-8">
<title>Brellwick Partners, LLC — Stationery</title>
<link href="https://fonts.googleapis.com/css2?family=Questrial&display=swap" rel="stylesheet">
<style>
  :root {
    --bg: #e9e9e9;
    --paper: #f1f1f1;
    --navy: #1f4a73;
    --navy-deep: #0d3660;
    --red: #c0272d;
    --ink: #555a60;
    --rule: #b8b8b8;
  }
  * { margin: 0; padding: 0; box-sizing: border-box; }
  html, body { width: 1200px; height: 821px; overflow: hidden; background: var(--bg); }
  body { position: relative; font-family: "Questrial", Arial, sans-serif; color: var(--ink); }

  .sheet { position: absolute; background: var(--paper); box-shadow: 0 2px 6px rgba(0,0,0,.12); overflow: hidden; }
  .letterhead { left: 70px; top: 110px; width: 466px; height: 662px; }
  .envelope-front { left: 612px; top: 224px; width: 524px; height: 250px; }
  .envelope-back { left: 618px; top: 515px; width: 524px; height: 247px; }

  .corner-band { position: absolute; left: 0; top: 0; }

  .brand { position: absolute; display: flex; align-items: center; gap: 6px; }
  .brand-mark { width: 9px; height: 9px; background: var(--red); flex: none; }
  .brand-name { font-size: 14px; color: var(--navy); letter-spacing: .4px; text-transform: uppercase; white-space: nowrap; }
  .letterhead .brand { left: 54px; top: 58px; }
  .envelope-front .brand { left: 58px; top: 52px; }

  .return-address { position: absolute; left: 58px; top: 150px; font-size: 8px; line-height: 12px; color: var(--ink); }
  .return-address { top: 150px; }
  .envelope-front .return-address { top: 149px; left: 59px; }

  .footer { position: absolute; left: 78px; top: 622px; display: flex; align-items: stretch; font-size: 7.5px; line-height: 11.5px; }
  .footer-block { padding: 0 14px; }
  .footer-block:first-child { padding-left: 0; }
  .footer-block + .footer-block { border-left: 1px solid var(--rule); }
  .footer-block:nth-child(2) { border-left-color: #8a8f96; }
  .footer-block:nth-child(3) { border-left-color: var(--red); }
  .contact-line { display: flex; align-items: center; gap: 4px; white-space: nowrap; }
  .contact-line svg { width: 7px; height: 7px; fill: var(--navy); flex: none; }

  .flap { position: absolute; left: 2px; top: 0; width: 520px; height: 87px; background: var(--navy-deep); border-radius: 0 0 12px 12px; display: flex; align-items: center; justify-content: center; gap: 6px; }
  .flap .brand-name { color: #ffffff; font-size: 12px; }
</style>
</head>
<body>

<section class="sheet letterhead" aria-label="Letterhead">
  <svg class="corner-band" width="60" height="142" viewBox="0 0 60 142"><polygon points="0,0 60,0 0,142" fill="var(--navy)"/></svg>
  <div class="brand"><span class="brand-mark"></span><span class="brand-name">Brellwick Partners, LLC</span></div>

  <footer class="footer">
    <div class="footer-block">
      <div>412 Linden Hollow Road</div>
      <div>Fairbury, Alaska 34512</div>
    </div>
    <div class="footer-block">
      <div class="contact-line"><svg viewBox="0 0 10 10"><path d="M2 0.5 L3.8 2.6 3 3.8 Q4.2 6 6.2 7 L7.4 6.2 9.5 8 8.5 9.5 Q3.5 9 0.5 1.5 Z"/></svg>555 214 7730</div>
      <div class="contact-line"><svg viewBox="0 0 10 10"><rect x="2.5" y="0.5" width="5" height="3"/><rect x="0.5" y="4" width="9" height="4" rx="1"/><rect x="2.5" y="7" width="5" height="2.5"/></svg>555 214 7731</div>
    </div>
    <div class="footer-block">
      <div class="contact-line"><svg viewBox="0 0 10 10"><rect x="0.5" y="2" width="9" height="6.5"/><path d="M0.5 2 L5 5.5 9.5 2" stroke="#fff" stroke-width="1" fill="none"/></svg>hello@brellwick.com</div>
      <div class="contact-line"><svg viewBox="0 0 10 10"><circle cx="5" cy="5" r="4.5"/><path d="M0.5 5 H9.5 M5 0.5 Q2.5 5 5 9.5 M5 0.5 Q7.5 5 5 9.5" stroke="#fff" stroke-width=".8" fill="none"/></svg>www.brellwick.com</div>
    </div>
  </footer>
</section>

<section class="sheet envelope-front" aria-label="Envelope front">
  <svg class="corner-band" width="49" height="116" viewBox="0 0 49 116"><polygon points="0,0 49,0 0,116" fill="var(--navy)"/></svg>
  <div class="brand"><span class="brand-mark"></span><span class="brand-name">Brellwick Partners, LLC</span></div>
  <address class="return-address" style="font-style:normal; top:74px; left:59px;">
    412 Linden Hollow Road<br>Fairbury, Alaska 34512
  </address>
</section>

<section class="sheet envelope-back" aria-label="Envelope back">
  <div class="flap"><span class="brand-mark"></span><span class="brand-name">Brellwick Partners, LLC</span></div>
</section>

</body>
</html>
```